KLV Plant Services

We are a heavy diesel mechanical business with additional air con certificates, remapping engine rebuilt

Contact Information for Business Card

Company Name, Director Name, Managing Director, Contact details, email and website

Font styles to use
Serif
Script

```html
<!DOCTYPE html>
<html lang="en">
<head>
<meta charset="utf-8">
<title>KLV Plant Services – Business Card</title>
<link href="https://fonts.googleapis.com/css2?family=Roboto:ital,wght@0,400;0,700;1,400&display=swap" rel="stylesheet">
<style>
  :root{
    --stage:#2b2b2d;
    --navy:#0b0a6e;
    --white:#ffffff;
    --grey:#c9c9d4;
  }
  *{box-sizing:border-box;margin:0;padding:0}
  html,body{width:1200px;height:875px;overflow:hidden}
  body{background:var(--stage);font-family:"Roboto",Arial,sans-serif;position:relative}

  .card{position:absolute;width:540px;height:310px;border-radius:22px;overflow:hidden;box-shadow:0 18px 40px rgba(0,0,0,.45)}

  /* front */
  .card--front{left:70px;top:110px;background:var(--white);display:flex;align-items:center;justify-content:center}
  .brand__name{color:var(--navy);font-weight:700;font-size:36px;line-height:1;white-space:nowrap}

  /* back */
  .card--back{left:590px;top:455px;background:var(--navy)}
  .back__art{position:absolute;right:0;top:0;width:230px;height:100%;
    background:linear-gradient(120deg,var(--grey) 0%,var(--white) 45%,var(--white) 100%);
    clip-path:polygon(22% 0,100% 0,100% 100%,0 100%)}
  .back__brand{position:absolute;right:20px;top:142px;color:var(--navy);font-weight:700;font-size:19px;line-height:1;white-space:nowrap}

  .contact{position:absolute;left:34px;top:36px;color:var(--white)}
  .contact__name{font-weight:700;font-size:25px;letter-spacing:.5px;text-transform:uppercase;line-height:1.2}
  .contact__role{font-style:italic;font-size:16px;margin-top:2px}
  .contact__rule{width:90px;height:2px;background:var(--white);margin:12px 0 14px 20px}
  .contact__list{list-style:none;font-size:13.5px;line-height:1.3}
  .contact__item{display:flex;gap:10px;align-items:flex-start;margin-bottom:4px}
  .contact__item svg{flex:none;width:13px;height:13px;margin-top:2px;fill:var(--white)}
  .contact__company{font-weight:700}
</style>
</head>
<body>

  <section class="card card--front">
    <span class="brand__name">KLV Plant Services</span>
  </section>

  <section class="card card--back">
    <div class="back__art" role="img" aria-label="Large white excavator arm and bucket illustration"></div>
    <div class="back__brand">KLV Plant Services</div>

    <div class="contact">
      <h1 class="contact__name">Daniel Reeve</h1>
      <p class="contact__role">Managing Director</p>
      <div class="contact__rule"></div>
      <ul class="contact__list">
        <li class="contact__item">
          <svg viewBox="0 0 24 24"><path d="M12 2a7 7 0 0 0-7 7c0 5 7 13 7 13s7-8 7-13a7 7 0 0 0-7-7zm0 9.5A2.5 2.5 0 1 1 12 6a2.5 2.5 0 0 1 0 5.5z"/></svg>
          <span><span class="contact__company">KLV Plant Services</span><br>18 Foundry Lane<br>Millbrook, Westshire, 40210</span>
        </li>
        <li class="contact__item">
          <svg viewBox="0 0 24 24"><path d="M6.6 10.8a15 15 0 0 0 6.6 6.6l2.2-2.2a1 1 0 0 1 1-.25 11.4 11.4 0 0 0 3.6.57 1 1 0 0 1 1 1V20a1 1 0 0 1-1 1A17 17 0 0 1 3 4a1 1 0 0 1 1-1h3.5a1 1 0 0 1 1 1c0 1.25.2 2.45.57 3.57a1 1 0 0 1-.25 1z"/></svg>
          <span>(555) 310-2740</span>
        </li>
        <li class="contact__item">
          <svg viewBox="0 0 24 24"><path d="M7 1h10a2 2 0 0 1 2 2v18a2 2 0 0 1-2 2H7a2 2 0 0 1-2-2V3a2 2 0 0 1 2-2zm0 3v14h10V4z"/></svg>
          <span>(555) 310-2741</span>
        </li>
        <li class="contact__item">
          <svg viewBox="0 0 24 24"><path d="M6 2h12v6H6zM3 9h18v9h-3v4H6v-4H3zm5 6v5h8v-5z"/></svg>
          <span>(555) 310-2742</span>
        </li>
        <li class="contact__item">
          <svg viewBox="0 0 24 24"><path d="M2 5h20v14H2zm2 2v.5l8 5 8-5V7z"/></svg>
          <span>hello@klvplant.example</span>
        </li>
        <li class="contact__item">
          <svg viewBox="0 0 24 24"><path d="M12 2a10 10 0 1 0 0 20 10 10 0 0 0 0-20zm6.9 9h-3a15 15 0 0 0-1.4-6A8 8 0 0 1 18.9 11zM12 4c.9 1.2 1.8 3.8 1.9 7h-3.8C10.2 7.8 11.1 5.2 12 4zM9.5 5a15 15 0 0 0-1.4 6h-3A8 8 0 0 1 9.5 5zm-4.4 8h3a15 15 0 0 0 1.4 6 8 8 0 0 1-4.4-6zm6.9 7c-.9-1.2-1.8-3.8-1.9-7h3.8c-.1 3.2-1 5.8-1.9 7zm2.5-1a15 15 0 0 0 1.4-6h3a8 8 0 0 1-4.4 6z"/></svg>
          <span>klvplant.example</span>
        </li>
      </ul>
    </div>
  </section>

</body>
</html>
```